New Business Card Design Project

We require a business card design for Vexalund, a newly established Indian company.
Our focus is on the development, manufacturing, and export of a diverse array of pharmaceutical products on a global scale. The card should convey a professional appearance, as our primary markets are in Africa, China, and Southeast Asian nations.
We envision a two-sided business card, with the reverse side dedicated to a logo set against a solid color or an elegantly designed pattern. The corners should be rounded. We would appreciate seeing both horizontal and vertical design options. We trust the designer to utilize their expertise in creating this design.

The content for the business card is included in the attached Word file.

Target Market(s)

Our primary markets are in Africa, China, and Southeast Asian, Latin America, Maldives, Sri Lanka

Industry/Entity Type

Pharmaceutical Manufacturing and Export

Contact Information for Business Card

Colors

Designer to choose colors to be used in the design.

Requirements
Must have
• The reverse side of the business card features solely the logo along with the tagline, "Care Beyond Borders."
Should not have
• The logo should not exceed two instances, encompassing both the front and back sides of the card.

```html
<!DOCTYPE html>
<html lang="en">
<head>
<meta charset="utf-8">
<title>Vexalund Business Card</title>
<link rel="stylesheet" href="https://fonts.googleapis.com/css2?family=Poppins:wght@400;700&family=Open+Sans:wght@400;600;700&display=swap">
<style>
  :root {
    --bg: #222222;
    --card: #ffffff;
    --brand-blue: #2ea7e0;
    --brand-coral: #f0624d;
    --ink: #1a1a1a;
    --card-w: 520px;
    --card-h: 300px;
    --radius: 28px;
  }
  * { box-sizing: border-box; margin: 0; padding: 0; }
  html, body { width: 1200px; height: 711px; overflow: hidden; background: var(--bg); }
  .canvas {
    width: 1200px; height: 711px;
    display: flex; align-items: center; justify-content: center; gap: 60px;
  }
  .card {
    position: relative;
    width: var(--card-w); height: var(--card-h);
    background: var(--card);
    border-radius: var(--radius);
    box-shadow: 0 0 0 4px var(--brand-blue), 0 18px 30px rgba(0,0,0,.55);
    overflow: hidden;
  }
  /* Reverse side */
  .card--back {
    display: flex; align-items: center; justify-content: center;
  }
  .back__lockup {
    display: flex; flex-direction: column; align-items: flex-end;
  }
  .brand {
    display: flex; align-items: center; gap: 12px;
    font-family: "Poppins", sans-serif; font-weight: 700;
    color: var(--brand-blue); line-height: 1.1;
  }
  .brand__dot { border-radius: 50%; background: var(--brand-coral); flex: none; }
  .card--back .brand { font-size: 58px; letter-spacing: 0.5px; }
  .card--back .brand__dot { width: 22px; height: 22px; }
  .tagline {
    margin-top: 6px;
    font-family: "Poppins", sans-serif; font-weight: 400;
    font-size: 13px; color: var(--ink); letter-spacing: 0.5px;
  }
  /* Front side */
  .card--front { display: flex; }
  .front__brand-area {
    width: 240px; display: flex; align-items: center; justify-content: center;
  }
  .card--front .brand { font-size: 36px; gap: 8px; }
  .card--front .brand__dot { width: 14px; height: 14px; }
  .front__divider {
    width: 1px; background: var(--brand-blue);
    margin: 48px 0 36px;
  }
  .front__details {
    flex: 1; padding: 58px 24px 0 26px;
    font-family: "Open Sans", sans-serif; color: var(--ink);
  }
  .person__name { font-size: 24px; color: var(--brand-blue); font-weight: 400; line-height: 1.1; }
  .person__first { font-weight: 700; }
  .person__role { font-size: 12px; font-weight: 600; margin-top: 2px; }
  .rule {
    height: 1.5px; margin: 8px 0;
    background: linear-gradient(90deg, var(--brand-coral), rgba(240,98,77,0));
  }
  .address { font-size: 11.5px; line-height: 1.45; }
  .contact { list-style: none; font-size: 11.5px; }
  .contact__item { display: flex; align-items: center; gap: 8px; line-height: 1.7; }
  .contact__icon { width: 13px; height: 13px; flex: none; }
</style>
</head>
<body>
<main class="canvas">
  <section class="card card--back" aria-label="Card reverse side">
    <div class="back__lockup">
      <div class="brand"><span class="brand__dot"></span>Vexalund</div>
      <p class="tagline">Care Beyond Borders.</p>
    </div>
  </section>

  <section class="card card--front" aria-label="Card front side">
    <div class="front__brand-area">
      <div class="brand"><span class="brand__dot"></span>Vexalund</div>
    </div>
    <div class="front__divider"></div>
    <div class="front__details">
      <h1 class="person__name"><span class="person__first">Rohan</span> K. Malvi</h1>
      <p class="person__role">CEO</p>
      <div class="rule"></div>
      <p class="address">14, Nilgiri Enclave,<br>Akola, 444001, India</p>
      <div class="rule"></div>
      <ul class="contact">
        <li class="contact__item">
          <svg class="contact__icon" viewBox="0 0 14 14"><rect x="3" y="1" width="8" height="12" rx="1.5" fill="none" stroke="var(--brand-coral)" stroke-width="1.4"/><circle cx="7" cy="11" r="0.8" fill="var(--brand-coral)"/></svg>
          +91 98765 43120
        </li>
        <li class="contact__item">
          <svg class="contact__icon" viewBox="0 0 14 14"><circle cx="7" cy="7" r="5.8" fill="none" stroke="var(--brand-blue)" stroke-width="1.3"/><ellipse cx="7" cy="7" rx="2.4" ry="5.8" fill="none" stroke="var(--brand-blue)" stroke-width="1"/><line x1="1.2" y1="7" x2="12.8" y2="7" stroke="var(--brand-blue)" stroke-width="1"/></svg>
          www.vexalund.com
        </li>
        <li class="contact__item">
          <svg class="contact__icon" viewBox="0 0 14 14"><rect x="1" y="3" width="12" height="8.5" rx="1" fill="none" stroke="var(--brand-coral)" stroke-width="1.3"/><polyline points="1.5,3.5 7,8 12.5,3.5" fill="none" stroke="var(--brand-coral)" stroke-width="1.3"/></svg>
          rmalvi@vexalund.com
        </li>
      </ul>
    </div>
  </section>
</main>
</body>
</html>
```